Heritage Hollow Business Cards

Require a business card design. <br/><br/>Needs to include logo (either round or long version) plus these details:<br/>Maya Torvell<br/>Heritage Hollow<br/>maya@kelvadtrading.com.au<br/>02 6481 7395<br/>PO Box Glenwarra NSW 2791<br/>www.heritagehollow.com.au<br/><br/>I need in an editable format so that I can create for multiple staff members. <br/><br/>

Target Market(s)

We are an online store selling renovation products to home owners are builders. Looking for a classic classy design.

Industry/Entity Type

Home And Garden

Contact Information for Business Card

Maya Torvell
Heritage Hollow
maya@kelvadtrading.com.au
02 6481 7395
PO Box Glenwarra NSW 2791
www.heritagehollow.com.au

Colors

Designer to choose colors to be used in the design.

Requirements
Must have
• Must include Logo.

```html
<!DOCTYPE html>
<html lang="en">
<head>
<meta charset="utf-8">
<title>Heritage Hollow Business Cards</title>
<link rel="stylesheet" href="https://fonts.googleapis.com/css2?family=Urbanist:wght@400;500;600&display=swap">
<style>
  :root {
    --backdrop: #4a4643;
    --card-green: #587565;
    --art-green-dark: #3f5a4c;
    --art-green-light: #5f7c6c;
    --brand-green: #3f5e4f;
    --paper: #ffffff;
    --ink: #1f1f1f;
    --on-green: #f4f4f0;
  }
  * { margin: 0; padding: 0; box-sizing: border-box; }
  html, body { width: 1200px; height: 900px; overflow: hidden; }
  body {
    background: var(--backdrop);
    font-family: "Urbanist", sans-serif;
    position: relative;
  }
  .card {
    position: absolute;
    left: 311px;
    width: 577px;
    height: 328px;
  }
  .card-front { top: 98px; background: var(--card-green); color: var(--on-green); }
  .card-back { top: 472px; background: var(--paper); color: var(--ink); }

  .front-artwork {
    position: absolute;
    left: 74px; top: 50px;
    width: 440px; height: 172px;
    border-radius: 4px;
    background: radial-gradient(ellipse at 50% 60%, var(--art-green-dark) 0%, var(--art-green-light) 75%, var(--card-green) 100%);
  }
  .front-name {
    position: absolute;
    left: 0; right: 0; top: 230px;
    text-align: center;
    font-size: 38px;
    font-weight: 500;
    line-height: 1.1;
    letter-spacing: 0.3px;
  }
  .front-web-row {
    position: absolute;
    left: 20px; right: 21px; top: 278px;
    display: flex; align-items: center; gap: 10px;
  }
  .front-web-row .rule { flex: 1; height: 1.5px; background: var(--on-green); }
  .front-web-row .web { font-size: 15px; }

  .back-brand {
    position: absolute;
    left: 36px; top: 84px;
    display: flex; align-items: center; gap: 10px;
    font-size: 27px; font-weight: 500; color: var(--ink);
  }
  .back-brand .mark {
    width: 16px; height: 16px; border-radius: 50%;
    background: var(--brand-green);
  }
  .person {
    position: absolute;
    right: 41px; top: 157px;
    text-align: right;
  }
  .person .name { font-size: 17px; font-weight: 600; color: var(--brand-green); }
  .person .company { font-size: 15px; margin-top: 0; }
  .divider {
    position: absolute;
    left: 35px; right: 41px; top: 206px;
    height: 1.5px; background: var(--brand-green);
  }
  .contacts {
    position: absolute;
    left: 34px; top: 218px;
    list-style: none;
  }
  .contacts li {
    display: flex; align-items: center; gap: 8px;
    font-size: 16px; height: 26.5px;
  }
  .contacts svg { width: 17px; height: 17px; fill: var(--brand-green); flex: none; }
  .address {
    position: absolute;
    right: 41px; top: 244px;
    text-align: right;
    font-size: 16px; line-height: 26.5px;
  }
</style>
</head>
<body>
  <section class="card card-front">
    <div class="front-artwork" role="img" aria-label="Sketched roof gable with chimney illustration"></div>
    <div class="front-name">Heritage Hollow</div>
    <div class="front-web-row">
      <span class="rule"></span>
      <span class="web">www.heritagehollow.com.au</span>
      <span class="rule"></span>
    </div>
  </section>

  <section class="card card-back">
    <div class="back-brand"><span class="mark"></span>Heritage Hollow</div>
    <div class="person">
      <div class="name">Maya Torvell</div>
      <div class="company">Heritage Hollow</div>
    </div>
    <div class="divider"></div>
    <ul class="contacts">
      <li>
        <svg viewBox="0 0 24 24" aria-hidden="true"><path d="M6.6 10.8a15.1 15.1 0 0 0 6.6 6.6l2.2-2.2c.3-.3.7-.4 1-.2 1.1.4 2.3.6 3.6.6.6 0 1 .4 1 1V20c0 .6-.4 1-1 1A17 17 0 0 1 3 4c0-.6.4-1 1-1h3.5c.6 0 1 .4 1 1 0 1.3.2 2.5.6 3.6.1.3 0 .7-.2 1z"/></svg>
        02 6481 7395
      </li>
      <li>
        <svg viewBox="0 0 24 24" aria-hidden="true"><path d="M3 5h18a1 1 0 0 1 1 1v.4l-10 6.3L2 6.4V6a1 1 0 0 1 1-1zm-1 3.7l10 6.3 10-6.3V18a1 1 0 0 1-1 1H3a1 1 0 0 1-1-1z"/></svg>
        maya@kelvadtrading.com.au
      </li>
      <li>
        <svg viewBox="0 0 24 24" aria-hidden="true"><path d="M12 2a10 10 0 1 0 0 20 10 10 0 0 0 0-20zm-1 17.9A8 8 0 0 1 4 12l5 5v1a2 2 0 0 0 2 2zm6.9-2.5A2 2 0 0 0 16 16h-1v-3a1 1 0 0 0-1-1H8v-2h2a1 1 0 0 0 1-1V7h2a2 2 0 0 0 2-2v-.4a8 8 0 0 1 2.9 12.8z"/></svg>
        www.heritagehollow.com.au
      </li>
    </ul>
    <div class="address">PO Box<br>Glenwarra NSW 2791</div>
  </section>
</body>
</html>
```